Brivolt Technologies business card design

We need a business card designed with our new logo. it would be great if the card could communicate it is a technology based company.

Target Market(s)

system integrators

Industry/Entity Type

technology, IOT

Contact Information for Business Card

Name, designation, Address, telephone number, email address

Requirements
Must have
• logo and company name
Nice to have
• something to do with technology

```html
<!DOCTYPE html>
<html lang="en">
<head>
<meta charset="utf-8">
<title>Brivolt Technologies – Business Card</title>
<link rel="stylesheet" href="https://fonts.googleapis.com/css2?family=Inter:wght@400;500;700;800&display=swap">
<style>
  :root {
    --stage: #1c1c1d;
    --card: #3a3a3b;
    --card-pattern-a: #2e2e2f;
    --card-pattern-b: #464647;
    --accent: #f7931e;
    --ink: #ffffff;
    --ink-soft: #e4e4e4;
  }
  * { box-sizing: border-box; margin: 0; padding: 0; }
  html, body {
    width: 1200px; height: 900px; overflow: hidden;
    background: var(--stage);
    font-family: "Inter", Arial, sans-serif;
  }
  .stage {
    width: 1200px; height: 900px;
    display: flex; flex-direction: column;
    align-items: center; justify-content: center; gap: 60px;
  }
  .card {
    position: relative;
    width: 630px; height: 360px;
    border-radius: 18px;
    background: var(--card);
    border-bottom: 2px solid var(--accent);
    box-shadow: 0 14px 30px rgba(0,0,0,.45);
    overflow: hidden;
  }
  /* Front */
  .card-front { display: flex; align-items: center; padding: 0 44px; }
  .brand { width: 290px; }
  .brand-name {
    display: flex; align-items: center; gap: 12px;
    color: var(--ink); font-weight: 800; font-size: 44px;
    letter-spacing: 1px; line-height: 1; text-transform: uppercase;
  }
  .brand-mark { width: 18px; height: 18px; background: var(--accent); flex: none; }
  .brand-tagline {
    margin: 8px 0 0 30px;
    color: var(--accent); font-weight: 500; font-size: 13px;
    letter-spacing: 7px; text-transform: uppercase;
  }
  .divider { width: 1.5px; height: 150px; background: var(--accent); margin: 0 28px 0 18px; }
  .contact { color: var(--ink-soft); font-size: 13.5px; line-height: 1.55; }
  .contact-name {
    color: var(--accent); font-weight: 700; font-size: 21px;
    text-transform: uppercase; letter-spacing: .5px; line-height: 1.2;
  }
  .contact-role { text-transform: uppercase; font-size: 13px; margin-bottom: 6px; }
  .contact-line { display: flex; align-items: center; gap: 7px; }
  .contact-line svg { width: 12px; height: 12px; flex: none; }
  /* Back */
  .card-back .pattern {
    position: absolute; inset: 0;
    background: linear-gradient(135deg, var(--card-pattern-b), var(--card-pattern-a) 55%, #252526);
  }
  .card-back .back-name {
    position: absolute; right: 40px; bottom: 34px;
    color: var(--ink); font-weight: 800; font-size: 22px;
    text-transform: uppercase; letter-spacing: 1px;
  }
</style>
</head>
<body>
<main class="stage">
  <section class="card card-front" aria-label="Business card front">
    <div class="brand">
      <div class="brand-name"><span class="brand-mark"></span>Brivolt</div>
      <div class="brand-tagline">Technologies</div>
    </div>
    <div class="divider"></div>
    <div class="contact">
      <div class="contact-name">Daniel Marsh</div>
      <div class="contact-role">Director</div>
      <div>4107 Cedar Bend Road</div>
      <div>Lansing, MI 48910</div>
      <div class="contact-line">
        <svg viewBox="0 0 24 24" fill="var(--accent)"><path d="M6.6 10.8a15 15 0 0 0 6.6 6.6l2.2-2.2a1 1 0 0 1 1-.25 11.4 11.4 0 0 0 3.6.57 1 1 0 0 1 1 1V20a1 1 0 0 1-1 1A17 17 0 0 1 3 4a1 1 0 0 1 1-1h3.5a1 1 0 0 1 1 1c0 1.25.2 2.45.57 3.57a1 1 0 0 1-.25 1z"/></svg>
        <span>(555) 318-4072</span>
      </div>
      <div class="contact-line">
        <svg viewBox="0 0 24 24" fill="none" stroke="var(--accent)" stroke-width="2"><rect x="3" y="5" width="18" height="14" rx="1"/><path d="M3 6l9 7 9-7"/></svg>
        <span>hello@brivolttech.com</span>
      </div>
      <div class="contact-line">
        <svg viewBox="0 0 24 24" fill="none" stroke="var(--accent)" stroke-width="2"><circle cx="12" cy="12" r="9"/><path d="M3 12h18M12 3c3 3 3 15 0 18M12 3c-3 3-3 15 0 18"/></svg>
        <span>brivolttech.com</span>
      </div>
    </div>
  </section>

  <section class="card card-back" aria-label="Business card back">
    <div class="pattern" role="img" aria-label="Repeating tonal pattern of the company symbol across the card back"></div>
    <div class="back-name">Brivolt</div>
  </section>
</main>
</body>
</html>
```